We are looking for Facebook and Instagram templates. To use both platforms we will use square images. We need a template for our posts, not the header image.
Most posts contain multiple images and we need a designoverlay in which we can embed our images.
Attached a screenshot of our website www.talurepo.be, our logo in svg and ai. The monkey is our mascotte (excact this monkey, not another).
We offer teambuildings, the style should be fun. Colors are antracite, limegreen and white. I did attache the current layout for posts but we are not happy with this.
If we could have some small design elements (like stickers) we can always create a new layout but is feels the same.
Our website is quite simple, this should also be in these post designs. Simple forms, rounded corners.
Updates

Allow more time for the designers, good work requires more time

Target Market(s)

Teambuilding

Industry/Entity Type

Teambuilding

Font styles to use
Other font styles liked:
• RobotoSlab

Requirements
Must have
• If we could have some small design elements (like stickers) we can always create a new layout but is feels the same.
Should not have
• Complex design, simple images works best for us

```html
<!DOCTYPE html>
<html lang="nl">
<head>
<meta charset="utf-8">
<title>Talurepo – social post templates</title>
<link href="https://fonts.googleapis.com/css2?family=Oswald:wght@500;600&family=Montserrat:wght@600;700&family=Roboto+Slab:wght@700&family=Great+Vibes&display=swap" rel="stylesheet">
<style>
  :root{
    --board:#6b6d65;
    --paper:#f1efea;
    --antracite:#2e2e2c;
    --antracite-soft:#3a3a37;
    --lime:#9ccb3b;
    --white:#ffffff;
    --forest:linear-gradient(160deg,#6f8f4a,#3f5a2c 60%,#8c8a76);
    --bar:linear-gradient(160deg,#4a3422,#a8743c 45%,#5a8a3a);
    --kids:linear-gradient(160deg,#e9b9c8,#e8d6a0 50%,#7c8fa8);
    --game:linear-gradient(160deg,#4f7a3a,#b23a36 50%,#d8ccb4);
    --house:linear-gradient(170deg,#f2f2ee,#a9a48e 45%,#4b4a3f);
    --wall:linear-gradient(160deg,#1d2a3a,#4f88c0 50%,#e9e4db);
  }
  *{margin:0;padding:0;box-sizing:border-box}
  html,body{width:1200px;height:843px;overflow:hidden}
  body{background:var(--board);position:relative;font-family:'Oswald',sans-serif}

  .post{position:absolute;width:321px;height:321px;background:var(--paper)}
  .post__inner{position:absolute;left:7px;top:7px;width:307px;height:307px;border-radius:9px;
    background:radial-gradient(circle at 30% 20%,var(--antracite-soft),var(--antracite) 70%);overflow:hidden}
  .post--1{left:96px;top:90px}.post--2{left:444px;top:90px}.post--3{left:790px;top:90px}
  .post--4{left:96px;top:433px}.post--5{left:444px;top:433px}.post--6{left:790px;top:433px}

  .photo{position:absolute;border:2px solid var(--lime);border-radius:4px}
  .photo--white{border-color:var(--white)}
  .photo--polaroid{border:4px solid var(--white);border-radius:3px;box-shadow:0 2px 5px rgba(0,0,0,.4)}
  .tone-forest{background:var(--forest)}.tone-bar{background:var(--bar)}.tone-kids{background:var(--kids)}
  .tone-game{background:var(--game)}.tone-house{background:var(--house)}.tone-wall{background:var(--wall)}

  .brand{position:absolute;display:flex;align-items:center;gap:4px;transform:translate(-50%,-50%);
    background:var(--antracite);padding:3px 7px;border-radius:3px}
  .brand__dot{width:6px;height:6px;background:var(--lime)}
  .brand__name{font-family:'Oswald',sans-serif;font-weight:600;font-size:15px;letter-spacing:1.5px;color:var(--white);line-height:1}

  .headline{position:absolute;font-family:'Oswald',sans-serif;font-weight:600;color:var(--white);text-transform:uppercase;line-height:1.05}
  .headline em{font-style:normal;color:var(--lime)}
  .script{position:absolute;font-family:'Great Vibes',cursive;color:var(--white);line-height:1.1}
  .caption{position:absolute;font-family:'Oswald',sans-serif;font-size:5px;color:var(--white);text-transform:uppercase}

  .url{position:absolute;transform:translate(-50%,-50%);background:var(--white);color:var(--antracite);
    font-family:'Montserrat',sans-serif;font-weight:700;font-size:7.5px;letter-spacing:.6px;
    height:14px;padding:0 10px;border-radius:8px;display:flex;align-items:center;gap:4px;white-space:nowrap}
  .url svg{width:6px;height:6px}

  .divider{position:absolute;height:1px;background:var(--lime)}

  .banner{position:absolute;left:18px;top:269px;width:285px;height:32px;background:var(--lime);
    border:2px solid var(--white);border-top:none;border-radius:0 0 5px 5px;text-align:center;color:var(--antracite)}
  .banner__title{font-family:'Roboto Slab',serif;font-weight:700;font-size:13px;letter-spacing:1px;line-height:1;margin-top:5px}
  .banner__sub{font-family:'Montserrat',sans-serif;font-weight:700;font-size:7px;letter-spacing:.4px;margin-top:2px}
</style>
</head>
<body>

<!-- post 1: six-photo grid -->
<section class="post post--1"><div class="post__inner">
  <div class="photo tone-forest" style="left:32px;top:24px;width:77px;height:83px" role="img" aria-label="Terrace with pavilion in the woods"></div>
  <div class="photo tone-kids" style="left:115px;top:24px;width:77px;height:83px" role="img" aria-label="Team solving a puzzle on the floor"></div>
  <div class="photo tone-game" style="left:197px;top:24px;width:77px;height:83px" role="img" aria-label="Tug of war in kilts"></div>
  <div class="photo tone-wall" style="left:32px;top:112px;width:77px;height:87px" role="img" aria-label="Player at a game wall"></div>
  <div class="photo tone-bar" style="left:115px;top:112px;width:77px;height:87px" role="img" aria-label="Guests at the bar"></div>
  <div class="photo tone-house" style="left:197px;top:112px;width:77px;height:87px" role="img" aria-label="Chalet building in the sun"></div>
  <div class="divider" style="left:32px;top:228px;width:243px"></div>
  <div class="brand" style="left:153px;top:228px"><span class="brand__dot"></span><span class="brand__name">TALUREPO</span></div>
  <div class="headline" style="left:0;width:307px;text-align:center;top:254px;font-size:18px"><em>Lorem</em> Ipsum ist einfach</div>
  <div class="url" style="left:157px;top:292px"><svg viewBox="0 0 10 10"><circle cx="5" cy="5" r="4" fill="none" stroke="currentColor" stroke-width="1.2"/></svg>www.talurepo.be</div>
</div></section>

<!-- post 2: two photos with headline -->
<section class="post post--2"><div class="post__inner">
  <div style="position:absolute;left:0;top:0;width:307px;height:196px;border:3px solid var(--lime);border-radius:9px 9px 12px 0;overflow:hidden;display:flex">
    <div class="tone-forest" style="width:153px;height:100%;border-right:3px solid var(--lime)" role="img" aria-label="Terrace with pavilion in the woods"></div>
    <div class="tone-bar" style="flex:1;height:100%" role="img" aria-label="Guests at the bar"></div>
  </div>
  <div class="brand" style="left:151px;top:187px"><span class="brand__dot"></span><span class="brand__name">TALUREPO</span></div>
  <div class="headline" style="left:18px;top:223px;font-size:26px"><em>Lorem</em> Ipsum<br>ist einfach</div>
  <div class="script" style="left:193px;top:236px;font-size:16px">Lorem Ipsum<br>&nbsp;ist einfach</div>
  <div class="url" style="left:153px;top:294px"><svg viewBox="0 0 10 10"><circle cx="5" cy="5" r="4" fill="none" stroke="currentColor" stroke-width="1.2"/></svg>www.talurepo.be</div>
</div></section>

<!-- post 3: single photo announcement -->
<section class="post post--3"><div class="post__inner">
  <div class="photo photo--white tone-game" style="left:18px;top:44px;width:285px;height:226px;border-bottom:none;border-radius:5px 5px 0 0" role="img" aria-label="Team playing tug of war in kilts on sand"></div>
  <div class="banner">
    <div class="banner__title">INZET BOUWVERLOF</div>
    <div class="banner__sub">Full house met de inzet van zomervakantie</div>
  </div>
  <div class="brand" style="left:152px;top:44px;border:1.5px solid var(--white)"><span class="brand__dot"></span><span class="brand__name">TALUREPO</span></div>
</div></section>

<!-- post 4: three framed photos -->
<section class="post post--4"><div class="post__inner">
  <div class="headline" style="left:14px;top:24px;font-size:24px"><em>Lorem</em> Ipsum<br>ist einfach</div>
  <div class="brand" style="left:248px;top:44px;border:1.5px solid var(--white)"><span class="brand__dot"></span><span class="brand__name">TALUREPO</span></div>
  <div class="photo tone-wall" style="left:13px;top:90px;width:86px;height:150px" role="img" aria-label="Player at a game wall"></div>
  <div class="photo tone-bar" style="left:101px;top:107px;width:103px;height:169px" role="img" aria-label="Guests at the bar"></div>
  <div class="photo tone-house" style="left:207px;top:90px;width:85px;height:150px" role="img" aria-label="Chalet building in the sun"></div>
  <div class="caption" style="left:24px;top:254px">Lorem ipsum ist einfach</div>
  <div class="caption" style="left:219px;top:254px">Lorem ipsum ist einfach</div>
  <div class="url" style="left:159px;top:292px"><svg viewBox="0 0 10 10"><circle cx="5" cy="5" r="4" fill="none" stroke="currentColor" stroke-width="1.2"/></svg>www.talurepo.be</div>
</div></section>

<!-- post 5: hero photo with polaroids -->
<section class="post post--5"><div class="post__inner">
  <div class="tone-bar" style="position:absolute;left:0;top:0;width:307px;height:177px;border-radius:0 0 14px 14px" role="img" aria-label="Guests at the bar"></div>
  <div class="brand" style="left:153px;top:25px;border:1.5px solid var(--white)"><span class="brand__dot"></span><span class="brand__name">TALUREPO</span></div>
  <div class="photo photo--polaroid tone-kids" style="left:17px;top:142px;width:88px;height:88px;transform:rotate(-6deg)" role="img" aria-label="Team solving a puzzle on the floor"></div>
  <div class="photo photo--polaroid tone-forest" style="left:108px;top:138px;width:89px;height:88px" role="img" aria-label="Terrace with pavilion in the woods"></div>
  <div class="photo photo--polaroid tone-game" style="left:199px;top:142px;width:88px;height:88px;transform:rotate(6deg)" role="img" aria-label="Tug of war in kilts"></div>
  <div class="headline" style="left:0;width:307px;text-align:center;top:237px;font-size:20px"><em>Lorem</em> Ipsum ist einfach</div>
  <div class="script" style="left:0;width:307px;text-align:center;top:262px;font-size:13px">Lorem Ipsum ist einfach</div>
  <div class="url" style="left:153px;top:293px"><svg viewBox="0 0 10 10"><circle cx="5" cy="5" r="4" fill="none" stroke="currentColor" stroke-width="1.2"/></svg>www.talurepo.be</div>
</div></section>

<!-- post 6: tilted photo stack -->
<section class="post post--6"><div class="post__inner">
  <div class="brand" style="left:54px;top:29px;border:1.5px solid var(--white)"><span class="brand__dot"></span><span class="brand__name">TALUREPO</span></div>
  <div class="headline" style="left:10px;top:64px;font-size:23px;line-height:1.08">Lorem<br><em>Ipsum ist<br>einfach</em></div>
  <div class="script" style="left:10px;top:142px;font-size:19px">Blindtext</div>
  <div class="photo photo--polaroid tone-bar" style="left:104px;top:58px;width:190px;height:198px;transform:rotate(4deg)" role="img" aria-label="Guests at the bar"></div>
  <div class="photo photo--polaroid tone-kids" style="left:10px;top:196px;width:95px;height:92px;transform:rotate(-5deg)" role="img" aria-label="Team solving a puzzle on the floor"></div>
  <div class="photo photo--polaroid tone-forest" style="left:101px;top:192px;width:86px;height:90px;transform:rotate(4deg)" role="img" aria-label="Terrace with pavilion in the woods"></div>
  <div class="url" style="left:159px;top:293px"><svg viewBox="0 0 10 10"><circle cx="5" cy="5" r="4" fill="none" stroke="currentColor" stroke-width="1.2"/></svg>www.talurepo.be</div>
</div></section>

</body>
</html>
```